Kestrel Facilities Business Card Design

We would now like to design business cards with the new Kestrel Facilities logo

Target Market(s)

Professional

Industry/Entity Type

Professional services

Contact Information for Business Card

Employee name, title, phone number, email address, corporate office address and logo.

Font styles to use
Sans Serif

Colors
0054AA
0677BA
7BADD7
CADEEF
E8F1F8

Requirements
Must have
• My logo
Should not have
• any other pictures or images besides my logo

```html
<!DOCTYPE html>
<html lang="en">
<head>
<meta charset="utf-8">
<title>Kestrel Facilities Business Card</title>
<link rel="stylesheet" href="https://fonts.googleapis.com/css2?family=Figtree:wght@400;500;700&display=swap">
<style>
  :root {
    --brand-blue: #3677be;
    --wave-grey: #a09fa0;
    --ink: #1a1a1a;
    --card: #ffffff;
    --backdrop: #8a8a8a;
  }
  * { box-sizing: border-box; margin: 0; padding: 0; }
  html, body { width: 1160px; height: 1200px; overflow: hidden; }
  body {
    background: var(--backdrop);
    font-family: "Figtree", Arial, sans-serif;
    position: relative;
  }
  .card {
    position: absolute;
    left: 199px;
    width: 777px;
    height: 441px;
    background: var(--card);
    overflow: hidden;
  }
  .card--front { top: 105px; }
  .card--back { top: 634px; }

  .card__waves {
    position: absolute;
    inset: 0;
    width: 100%;
    height: 100%;
  }
  .wordmark {
    position: absolute;
    display: flex;
    align-items: center;
    color: var(--brand-blue);
    font-weight: 700;
    line-height: 1.02;
  }
  .wordmark__square {
    background: var(--brand-blue);
    flex: none;
  }
  .card--front .wordmark { left: 73px; top: 92px; gap: 18px; font-size: 44px; }
  .card--front .wordmark__square { width: 70px; height: 70px; }
  .card--back .wordmark { left: 237px; top: 138px; gap: 22px; font-size: 54px; }
  .card--back .wordmark__square { width: 86px; height: 86px; }

  .divider {
    position: absolute;
    left: 418px;
    top: 54px;
    width: 2px;
    height: 255px;
    background: var(--brand-blue);
  }
  .contact {
    position: absolute;
    left: 469px;
    top: 50px;
    color: var(--ink);
  }
  .contact__name {
    color: var(--brand-blue);
    font-weight: 700;
    font-size: 31px;
    letter-spacing: 0.2px;
    line-height: 34px;
  }
  .contact__title {
    font-size: 21px;
    font-weight: 500;
    line-height: 26px;
  }
  .contact__address {
    margin-top: 30px;
    font-size: 21px;
    font-weight: 500;
    line-height: 29px;
    font-style: normal;
  }
  .contact__list {
    list-style: none;
    margin-top: 26px;
  }
  .contact__item {
    display: flex;
    align-items: center;
    gap: 7px;
    font-size: 21px;
    font-weight: 500;
    line-height: 29.5px;
  }
  .contact__icon { width: 19px; height: 19px; fill: var(--brand-blue); flex: none; }
</style>
</head>
<body>
  <section class="card card--front" aria-label="Business card front">
    <svg class="card__waves" viewBox="0 0 777 441" preserveAspectRatio="none" aria-hidden="true">
      <path d="M0 336 C60 300 100 290 150 290 C300 290 480 385 600 385 C700 385 760 340 777 302 L777 316 C760 350 700 396 600 396 C480 396 300 305 150 305 C100 305 60 318 0 348 Z" fill="var(--wave-grey)"/>
      <path d="M0 354 C50 328 90 315 150 315 C300 315 480 396 600 396 C700 396 755 360 777 321 L777 441 L0 441 Z" fill="var(--brand-blue)"/>
    </svg>

    <div class="wordmark">
      <span class="wordmark__square"></span>
      <span class="wordmark__name">Kestrel<br>Facilities</span>
    </div>

    <div class="divider"></div>

    <div class="contact">
      <h1 class="contact__name">DANA WHITFIELD</h1>
      <p class="contact__title">Co-Founder</p>
      <address class="contact__address">4180 N. Harbor Lane<br>Suite 210 Ridgefield.14</address>
      <ul class="contact__list">
        <li class="contact__item">
          <svg class="contact__icon" viewBox="0 0 20 20" aria-hidden="true"><path d="M2 8 C2 4 18 4 18 8 L15 9 L14 7 H6 L5 9 Z"/><path d="M6 8 H14 L17 12 V17 H3 V12 Z"/></svg>
          <span>+254-700-41523</span>
        </li>
        <li class="contact__item">
          <svg class="contact__icon" viewBox="0 0 20 20" aria-hidden="true"><path d="M2 5 H18 V16 H2 Z M3 6.5 L10 11.5 L17 6.5 V6 H3 Z" fill-rule="evenodd"/></svg>
          <span>hello@kestrelfm.com</span>
        </li>
        <li class="contact__item">
          <svg class="contact__icon" viewBox="0 0 20 20" aria-hidden="true"><circle cx="10" cy="10" r="8.5"/><path d="M5 6 Q8 5 9 8 Q7 10 8 13 Q5 12 5 9 Z M12 4 Q15 6 15 10 Q13 12 12 9 Z" fill="#ffffff"/></svg>
          <span>www.kestrelfm.com</span>
        </li>
      </ul>
    </div>
  </section>

  <section class="card card--back" aria-label="Business card back">
    <div class="wordmark">
      <span class="wordmark__square"></span>
      <span class="wordmark__name">Kestrel<br>Facilities</span>
    </div>
  </section>
</body>
</html>
```